Mobile Friendly Lead Generation Landing Page

We are a web marketing company that specialized in web lead generation. Recently we have started buying media from mobile devices and we need a mobile interface(landing page) where we can collect user data in an effective manner.

Our current mobile landing page is:
http://www.tutorpath.example.com/lp13d/index.aspx?a=true&source=841356
Through this you can see what the steps/questions users need to answer to get matched to a school. We need the design for the whole process.

We are pretty open for design ideas and our goal is to make this mobile optimized landing page have the look and feel of an app...but not an app.
There are several questions in the process but we are open to changing the way they are presented. As in, you can have one question at a time or a few.
The goal is to make this EXTREMELY EASY for users to interact with.

One example that we have liked is:
http://learnvane.example/schools/57214-page1.lvne (please note that this opens only on mobile devices)

Some of these screenshots are attached.

Our web form looks like this:
http://www.tutorpath.example.com/lp88/index.aspx?a=true

```html
<!DOCTYPE html>
<html lang="en">
<head>
<meta charset="utf-8">
<title>Personal details – 2 minute form</title>
<link rel="stylesheet" href="https://fonts.googleapis.com/css2?family=Open+Sans:wght@300;400;600;700&display=swap">
<style>
  :root {
    --page-bg: #d9dcdf;
    --status-bg: #262b33;
    --header-bg: #3a4c62;
    --progress-bg: #243346;
    --seg-empty: #3b4f66;
    --seg-green: #3fa521;
    --seg-green-light: #7fce4d;
    --body-bg: #ececec;
    --card-bg: #ffffff;
    --field-bg: #f2f2f2;
    --field-line: #e1e1e1;
    --label: #9a9a9a;
    --title: #7b7b7b;
    --button: #7ac443;
    --white: #ffffff;
    --muted-light: #8a9bb0;
  }
  * { box-sizing: border-box; margin: 0; padding: 0; }
  html, body { width: 1200px; height: 999px; overflow: hidden; }
  body {
    background: var(--page-bg);
    font-family: "Open Sans", Arial, sans-serif;
    position: relative;
  }
  .screen {
    position: absolute;
    left: 340px; top: 38px;
    width: 520px; height: 922px;
    background: var(--body-bg);
    overflow: hidden;
    box-shadow: 0 6px 30px rgba(0,0,0,.18);
  }
  .status-bar {
    position: absolute; left: 0; top: 0; width: 100%; height: 32px;
    background: var(--status-bg); color: var(--white);
    font-size: 19px; font-weight: 600;
    display: flex; align-items: center; justify-content: space-between;
    padding: 0 14px;
  }
  .status-bar .carrier { display: flex; align-items: center; gap: 6px; }
  .status-bar .battery { display: flex; align-items: center; gap: 6px; }
  .app-header {
    position: absolute; left: 0; top: 32px; width: 100%; height: 76px;
    background: var(--header-bg); color: var(--white);
    display: flex; align-items: center; justify-content: center;
    font-size: 18px; font-weight: 300;
  }
  .app-header strong { font-weight: 700; }
  .nav-btn { position: absolute; top: 22px; }
  .nav-btn.back { left: 34px; }
  .nav-btn.forward { right: 18px; top: 14px; }
  .progress-panel {
    position: absolute; left: 0; top: 108px; width: 100%; height: 142px;
    background: var(--progress-bg);
  }
  .progress-track {
    position: absolute; left: 58px; top: 56px; width: 402px; height: 24px;
    display: flex; gap: 6px;
  }
  .segment { flex: 1; background: var(--seg-empty); }
  .segment.done { background: linear-gradient(180deg, var(--seg-green-light), var(--seg-green)); }
  .segment.half { background: linear-gradient(90deg, var(--seg-green-light) 0 50%, var(--seg-empty) 50% 100%); }
  .progress-label {
    position: absolute; top: 88px; width: 100%; text-align: center;
    font-size: 11px; color: var(--muted-light); font-weight: 300;
  }
  .form-card {
    position: absolute; left: 24px; top: 274px; width: 472px; height: 615px;
    background: var(--card-bg);
    box-shadow: 0 1px 3px rgba(0,0,0,.08);
  }
  .help { position: absolute; right: 12px; top: 10px; }
  .form-title {
    position: absolute; top: 26px; width: 100%; text-align: center;
    font-size: 25px; font-weight: 300; color: var(--title);
  }
  .field { position: absolute; left: 63px; width: 364px; }
  .field label { display: block; font-size: 13px; color: var(--label); font-weight: 300; height: 20px; }
  .input {
    height: 36px; background: var(--field-bg);
    border-bottom: 2px solid var(--field-line); position: relative;
  }
  .input .caret { position: absolute; right: 10px; top: 11px; }
  .phone-group { display: flex; gap: 5px; }
  .phone-group .input:nth-child(1) { flex: 56; }
  .phone-group .input:nth-child(2) { flex: 62; }
  .phone-group .input:nth-child(3) { flex: 104; }
  .next-btn {
    position: absolute; left: 80px; top: 526px; width: 314px; height: 58px;
    background: var(--button); color: var(--white);
    font-size: 23px; font-weight: 600;
    display: flex; align-items: center; justify-content: center; gap: 16px;
  }
</style>
</head>
<body>
  <main class="screen">
    <div class="status-bar">
      <span class="carrier">
        <svg width="20" height="14" viewBox="0 0 20 14"><rect x="0" y="9" width="3" height="5" fill="#fff"/><rect x="4" y="7" width="3" height="7" fill="#fff"/><rect x="8" y="5" width="3" height="9" fill="#fff"/><rect x="12" y="2" width="3" height="12" fill="#fff"/><rect x="16" y="0" width="3" height="14" fill="#fff"/></svg>
        Carrier
      </span>
      <span class="clock">10:35 AM</span>
      <span class="battery">
        <svg width="16" height="16" viewBox="0 0 16 16"><circle cx="8" cy="8" r="7" fill="#fff"/><path d="M8 4v4h3" stroke="#262b33" stroke-width="2" fill="none"/></svg>
        65%
        <svg width="30" height="14" viewBox="0 0 30 14"><rect x="1" y="1" width="25" height="12" fill="none" stroke="#fff" stroke-width="1.5"/><rect x="3" y="3" width="14" height="8" fill="#fff"/><rect x="27" y="4" width="2" height="6" fill="#fff"/></svg>
      </span>
    </div>

    <header class="app-header">
      <svg class="nav-btn back" width="30" height="30" viewBox="0 0 30 30"><circle cx="15" cy="15" r="13" fill="none" stroke="#c5d0dc" stroke-width="1.6"/><path d="M21 15H9M14 10l-5 5 5 5" fill="none" stroke="#c5d0dc" stroke-width="1.6"/></svg>
      <p>Fill out our <strong>2 MINUTE</strong> form!</p>
      <svg class="nav-btn forward" width="30" height="30" viewBox="0 0 30 30"><circle cx="15" cy="15" r="13" fill="none" stroke="#c5d0dc" stroke-width="1.6"/><path d="M9 15h12M16 10l5 5-5 5" fill="none" stroke="#c5d0dc" stroke-width="1.6"/></svg>
    </header>

    <section class="progress-panel">
      <div class="progress-track">
        <span class="segment done"></span>
        <span class="segment half"></span>
        <span class="segment"></span>
        <span class="segment"></span>
      </div>
      <p class="progress-label">progress: 76% completed</p>
    </section>

    <form class="form-card">
      <svg class="help" width="22" height="22" viewBox="0 0 22 22"><circle cx="11" cy="11" r="9.5" fill="none" stroke="#c8c8c8" stroke-width="1.2"/><text x="11" y="15" text-anchor="middle" font-size="12" fill="#b0b0b0" font-family="Open Sans, sans-serif">?</text></svg>
      <h1 class="form-title">Personal details :</h1>

      <div class="field" style="top:100px">
        <label>Salutation :</label>
        <div class="input"><svg class="caret" width="10" height="9" viewBox="0 0 10 9"><path d="M0 0h10L5 9z" fill="#b5b5b5"/></svg></div>
      </div>
      <div class="field" style="top:182px">
        <label>First Name :</label>
        <div class="input"></div>
      </div>
      <div class="field" style="top:264px">
        <label>Last Name :</label>
        <div class="input"></div>
      </div>
      <div class="field" style="top:346px">
        <label>Email :</label>
        <div class="input"></div>
      </div>
      <div class="field" style="top:428px">
        <label>Phone :</label>
        <div class="phone-group">
          <div class="input"></div>
          <div class="input"></div>
          <div class="input"></div>
        </div>
      </div>

      <div class="next-btn">Next
        <svg width="10" height="16" viewBox="0 0 10 16"><path d="M2 2l6 6-6 6" fill="none" stroke="#fff" stroke-width="2.4"/></svg>
      </div>
    </form>
  </main>
</body>
</html>
```